Web Site Design For Real Estate Sales Project

The idea behind this project is pretty simple. I am putting my penthouse apartment up for sale and am trying to be creative in selling it.
Technically this will be pretty simple, it will be 3 pages but graphically this has to be as impressive as possible which is why I am trying Pixel Harbor.
The apartment is located in Barra Da Tijuca, Rio De Janeiro, Brazil. (This is where the 2016 Solstice Meet will be held)
I am looking for an index page and 2 sub-pages. I am open to all kinds of designs and navigation's but it has to make an impression quickly with a professional and enticing design. The index page should make it obvious that there is a penthouse apartment for sale in Barra Da Tijuca ( suburb of Rio De Janeiro). The first sub page is about the Condominium where the apartment is located, the second sub page is about the apartment itself.
Here is a more detailed description of what the 3 pages should be about.
Index Page
This is the landing page and should make it obvious that there is an apartment for sale in Barra Da Tijuca, Rio De Janeiro with the following attributes
251 SQ M
Duplex Penthouse
4 suites
Price R$ 2.200.000
Price per SQ M: R$ 8.764
First Sub-Page
This is about the Condominium which is called "Tranquil Cliff Suites" with the following bullets
*Family friendly and safe
*Direct access to the beach
*Many amenities like pool, football court, gym, sauna
There should be some photos of the condominium and a link to the site of the condominium ( www.tcsqv.com )
Second Sub-page
This is about the apartment. It should list in bullets the features of the apartment and then have a photo gallery of the view and various rooms. I have attached sample photos but will eventually have to use more photos.
Apartment Features
Price: R$ 2.220.000
251 m2 Duplex Penthouse
4 suites
maids room with bath
guest bathroom
living room
dinning room
Terrace with heated pool for year round use
Veranda
As mentioned above I am open to all designs and navigation so feel free to be creative. The important thing is catch peoples attention and get the message across in a few seconds, which is that there is an apartment for sale at this price with these features in this location. I will then use zintra clickreach and SEO to get people to the site.
Thanks
Men and Women from 30-60 years of age.
Apartment

```html
<!DOCTYPE html>
<html lang="en">
<head>
<meta charset="utf-8">
<title>Skyline Residence</title>
<link href="https://fonts.googleapis.com/css2?family=PT+Sans:wght@400;700&display=swap" rel="stylesheet">
<style>
:root{
  --ink:#ffffff;
  --dark:#2b2b2b;
  --orange:#f7931e;
  --orange-deep:#e96f00;
  --blue:#3aa7dc;
  --blue-deep:#1e84c2;
  --panel:rgba(62,62,62,.82);
  --caption:rgba(110,110,110,.78);
  --yellow:#f2e200;
  --label:rgba(40,40,40,.85);
}
*{box-sizing:border-box;margin:0;padding:0}
html,body{width:1037px;height:1200px;overflow:hidden;background:#fff}
body{position:relative;font-family:"PT Sans",sans-serif;color:var(--ink)}
.hero{position:absolute;left:0;top:0;width:1037px;height:864px;
  background:linear-gradient(100deg,#5f6660 0%,#8a8578 30%,#b7ad97 48%,#d7ccb4 56%,#7fa7a3 68%,#4f8c92 85%,#3e7a86 100%)}
.hero-sky{position:absolute;left:0;top:0;width:1037px;height:150px;background:linear-gradient(180deg,#6f8a95,rgba(111,138,149,0))}
.site-header{position:absolute;left:43px;top:37px;width:963px;height:79px;background:linear-gradient(180deg,#2e2e2e,#0f0f0f)}
.brand{position:absolute;left:42px;top:22px;font-family:"PT Sans",sans-serif;font-weight:400;font-size:28px;color:#fff}
.nav-btn{position:absolute;top:20px;height:38px;border-radius:7px;font-size:12px;display:flex;align-items:center;justify-content:center;border:2px solid #fff3}
.nav-home{left:553px;width:71px;background:linear-gradient(180deg,var(--orange),var(--orange-deep));color:#2a1a00}
.nav-suites{left:637px;width:175px;background:linear-gradient(180deg,var(--blue),var(--blue-deep));color:#fff}
.nav-apartment{left:822px;width:114px;background:linear-gradient(180deg,var(--orange),var(--orange-deep));color:#2a1a00}
.dropdown{position:absolute;left:681px;top:105px;width:244px;height:202px;background:var(--blue);border:2px solid #fff;border-radius:6px}
.dropdown-notch{position:absolute;left:740px;top:96px}
.dropdown-photo{position:absolute;left:3px;top:3px;width:234px;height:136px;background:linear-gradient(180deg,#d9e6ef,#a9a59b 60%,#7d7a74);border-radius:4px 4px 0 0}
.dropdown-text{position:absolute;left:6px;top:144px;width:230px;font-size:9.5px;line-height:14px;text-align:justify;color:#fff}
.dropdown-more{position:absolute;right:14px;bottom:8px;font-size:9.5px;color:#10324a}
.caption{position:absolute;left:0;top:463px;width:597px;height:93px;background:var(--caption)}
.caption-text{position:absolute;left:39px;top:35px;font-size:16.5px;color:#fff}
.caption-arrows{position:absolute;left:534px;top:34px}
.welcome{position:absolute;left:46px;top:716px;width:574px;height:148px;background:var(--panel);border-radius:7px 7px 0 0}
.welcome h1{position:absolute;left:26px;top:13px;font-weight:400;font-size:14.5px;border-bottom:1px solid #aaa;padding-bottom:2px;padding-right:10px}
.welcome p{position:absolute;left:26px;top:41px;width:524px;font-size:9.6px;line-height:15.5px;text-align:justify;color:#e8e8e8}
.welcome-more{position:absolute;right:26px;bottom:10px;font-size:9.5px;color:var(--yellow)}
.facts{position:absolute;left:652px;top:716px;width:342px;height:148px;background:var(--panel);border-radius:7px 7px 0 0}
.facts ul{position:absolute;left:21px;top:35px;list-style:none;font-size:11.2px;line-height:17.4px}
.map{position:absolute;left:159px;top:24px;width:164px;height:106px;border-radius:6px;border:2px solid #fff;background:linear-gradient(135deg,#ebe7df,#f4f1ea 60%,#e4e1da)}
.features-ribbon{position:absolute;left:43px;top:886px;width:944px;height:45px}
.features-title{position:absolute;left:132px;top:892px;font-size:17px;font-weight:400;color:#2b2b2b}
.thumb{position:absolute;top:966px;width:153px;height:119px;border:1px solid #bbb;box-shadow:2px 2px 3px rgba(0,0,0,.25);overflow:hidden}
.thumb-photo{position:absolute;inset:0}
.thumb-label{position:absolute;left:0;right:0;bottom:0;height:29px;background:var(--label);font-size:11px;display:flex;align-items:center;justify-content:center;text-align:center;line-height:15px}
.thumb-label.tall{height:35px}
.site-footer{position:absolute;left:0;top:1121px;width:1037px;height:79px;background:var(--dark);border-top:2px solid #444}
.social{position:absolute;left:92px;top:28px;display:flex;gap:12px}
.social span{display:flex;align-items:center;gap:4px;font-size:9px;color:#cfcfcf}
.social i{display:block;width:14px;height:14px;background:#5b6f99}
.copyright{position:absolute;right:73px;top:30px;font-size:9.5px;color:#ddd}
</style>
</head>
<body>
<section class="hero" role="img" aria-label="Aerial photo of Barra Da Tijuca beachfront with high-rise towers, beach and ocean surf">
  <div class="hero-sky"></div>
</section>

<header class="site-header">
  <div class="brand">Skyline Residence</div>
  <nav>
    <div class="nav-btn nav-home">HOME</div>
    <div class="nav-btn nav-suites">TRANQUIL CLIFF SUITES</div>
    <div class="nav-btn nav-apartment">THE APARTMENT</div>
  </nav>
</header>

<svg class="dropdown-notch" width="30" height="12" viewBox="0 0 30 12"><path d="M0 11 L15 1 L30 11 Z" fill="#3aa7dc" stroke="#fff" stroke-width="2"/><rect x="1" y="10" width="28" height="3" fill="#3aa7dc"/></svg>
<div class="dropdown">
  <div class="dropdown-photo" role="img" aria-label="Condominium pool terrace with umbrellas and outdoor chairs"></div>
  <p class="dropdown-text">Sed ut perspiciatis unde omnis iste natus error sit voluptatem accusantium doloremque laudantium, totam rem aperiam.</p>
  <div class="dropdown-more">MORE &gt;&gt;</div>
</div>

<div class="caption">
  <p class="caption-text">I am selling my penthouse which is located at Barra Da Tijuca.</p>
  <svg class="caption-arrows" width="50" height="34" viewBox="0 0 50 34"><path d="M16 2 L4 17 L16 32" fill="none" stroke="#ddd" stroke-width="3"/><path d="M34 2 L46 17 L34 32" fill="none" stroke="#ddd" stroke-width="3"/></svg>
</div>

<section class="welcome">
  <h1>Welcome to Skyline Residence</h1>
  <p>Sed ut perspiciatis unde omnis iste natus error sit voluptatem accusantium doloremque laudantium, totam rem aperiam, eaque ipsa quae ab illo inventore veritatis et quasi architecto beatae vitae dicta sunt explicabo. Nemo enim ipsam voluptatem quia voluptas sit aspernatur aut odit aut fugit, sed quia consequuntur magni dolores eos qui ratione voluptatem sequi nesciunt. Neque porro quisquam est, qui dolorem ipsum quia dolor sit amet, consectetur, adipisci velit, sed quia non numquam eius modi tempora incidunt ut labore et dolore magnam aliquam quaerat voluptatem aliquid ex ea commodi consequatur.</p>
  <div class="welcome-more">MORE &gt;&gt;</div>
</section>

<section class="facts">
  <ul>
    <li>251 SQ M</li>
    <li>Duplex Penthouse</li>
    <li>4 suites</li>
    <li>Price R$ 2.200.000</li>
    <li>Price per SQ M: R$ 8.764</li>
  </ul>
  <div class="map" role="img" aria-label="Street map showing the apartment location near the beach"></div>
</section>

<svg class="features-ribbon" width="944" height="45" viewBox="0 0 944 45">
  <path d="M0 12 L62 12 L62 40 L4 40 L14 26 Z" fill="#e6e6e6" stroke="#c9c9c9"/>
  <path d="M882 12 L944 12 L934 26 L942 40 L882 40 Z" fill="#e6e6e6" stroke="#c9c9c9"/>
  <rect x="59" y="1" width="827" height="36" fill="#f4f4f4" stroke="#cfcfcf"/>
  <rect x="59" y="36" width="827" height="3" fill="#bdbdbd"/>
</svg>
<h2 class="features-title">Our Features</h2>

<div class="thumb" style="left:26px"><div class="thumb-photo" role="img" aria-label="Maids room with bath" style="background:linear-gradient(180deg,#d8d2c4,#8d8576)"></div><div class="thumb-label">MAIDS ROOM WITH BATH</div></div>
<div class="thumb" style="left:191px"><div class="thumb-photo" role="img" aria-label="Guest bathroom" style="background:linear-gradient(180deg,#c9c0b0,#6e3b32 55%,#3a3a3a)"></div><div class="thumb-label">GUEST BATHROOM</div></div>
<div class="thumb" style="left:356px"><div class="thumb-photo" role="img" aria-label="Living room" style="background:linear-gradient(180deg,#e6dccb,#a07a5a 60%,#5b4030)"></div><div class="thumb-label">LIVING ROOM</div></div>
<div class="thumb" style="left:521px"><div class="thumb-photo" role="img" aria-label="Dining room" style="background:linear-gradient(180deg,#d8d2c4,#8d8576)"></div><div class="thumb-label">DINNING ROOM</div></div>
<div class="thumb" style="left:686px"><div class="thumb-photo" role="img" aria-label="Terrace with heated pool" style="background:linear-gradient(180deg,#2f3a48,#5a6470 55%,#3fa9d8)"></div><div class="thumb-label tall">TERRACE WITH HEATED<br>POOL FOR YEAR ROUND USE</div></div>
<div class="thumb" style="left:851px"><div class="thumb-photo" role="img" aria-label="Veranda with view over the city" style="background:linear-gradient(180deg,#d9dde0,#a49585 55%,#6b5545)"></div><div class="thumb-label">VERANDA</div></div>

<footer class="site-footer">
  <div class="social">
    <span><i></i>Circlebook</span>
    <span><i></i>Chirpline</span>
    <span><i></i>Workweb</span>
    <span><i></i>Newsfeed</span>
  </div>
  <p class="copyright">© 2013 Skyline Residence., All Rights Reserved</p>
</footer>
</body>
</html>
```